Corporate Business Card

Very professional, Modern, Not to busy, include phone address email, website
(253) 617-4930, 18761 52nd Avenue S, Kent, WA 98047, martin@plumlinegroup.com, varkoworks.com

Target Market(s)

Manufacturing

Industry/Entity Type

Aero, machining, manufacturing, Off road racing

Contact Information for Business Card

Phone, address email, website

```html
<!DOCTYPE html>
<html lang="en">
<head>
<meta charset="utf-8">
<title>Varko Works – Business Card</title>
<link rel="stylesheet" href="https://fonts.googleapis.com/css2?family=Exo+2:wght@600;700&family=Roboto:wght@400&display=swap">
<style>
  :root {
    --page-bg: #2a2a2a;
    --front-top: #1c1c1d;
    --front-bottom: #2e2f31;
    --back-top: #2b3768;
    --back-bottom: #26325f;
    --brand-red: #d2262d;
    --ink-light: #eef0f5;
    --ink-soft: #dde1ec;
    --logo-grey: #6d6e71;
  }
  * { box-sizing: border-box; margin: 0; padding: 0; }
  html, body { width: 1200px; height: 1138px; overflow: hidden; }
  body { background: var(--page-bg); position: relative; font-family: "Roboto", Arial, sans-serif; }

  .card {
    position: absolute;
    left: 275px;
    width: 620px;
    height: 375px;
    border-radius: 16px;
    overflow: hidden;
  }
  .card--front {
    top: 186px;
    background: linear-gradient(160deg, var(--front-top) 0%, var(--front-top) 45%, var(--front-bottom) 100%);
  }
  .card--back {
    top: 608px;
    background: linear-gradient(180deg, var(--back-top) 0%, var(--back-bottom) 100%);
  }

  .brand-name {
    position: absolute;
    font-family: "Exo 2", Arial, sans-serif;
    font-weight: 700;
    text-transform: uppercase;
    white-space: nowrap;
  }
  .card--front .brand-name {
    left: 0; right: 0;
    top: 128px;
    text-align: center;
    font-size: 64px;
    letter-spacing: 2px;
    color: var(--logo-grey);
  }
  .card--back .brand-name {
    left: 42px;
    top: 72px;
    font-size: 36px;
    color: var(--ink-light);
  }

  .front-url {
    position: absolute;
    left: 0; right: 0;
    top: 326px;
    text-align: center;
    font-size: 16px;
    letter-spacing: 12px;
    color: var(--ink-light);
    padding-left: 12px;
  }
  .front-url .accent { color: var(--brand-red); }

  .person-name {
    position: absolute;
    right: 46px;
    top: 78px;
    font-family: "Exo 2", Arial, sans-serif;
    font-weight: 700;
    font-size: 26px;
    letter-spacing: 0.5px;
    text-transform: uppercase;
    color: var(--ink-light);
  }
  .person-name .surname { color: var(--brand-red); }

  .contact-list {
    position: absolute;
    right: 32px;
    top: 230px;
    list-style: none;
  }
  .contact-list li {
    display: flex;
    align-items: center;
    justify-content: flex-end;
    height: 24.5px;
    font-size: 17px;
    color: var(--ink-soft);
  }
  .contact-list svg {
    width: 15px; height: 15px;
    margin-left: 13px;
    fill: var(--brand-red);
    flex: none;
  }
</style>
</head>
<body>

<section class="card card--front" aria-label="Business card front">
  <div class="brand-name">Varko Works</div>
  <p class="front-url">www.varko<span class="accent">works</span>.com</p>
</section>

<section class="card card--back" aria-label="Business card back">
  <div class="brand-name">Varko Works</div>
  <h1 class="person-name">Martin <span class="surname">Hale</span></h1>

  <ul class="contact-list">
    <li>(253) 617-4930
      <svg viewBox="0 0 16 16" aria-hidden="true"><path d="M1 5c0-2 3-3 7-3s7 1 7 3v1.5h-3.5V5H4.5v1.5H1z M4 8l1.5-1.5h5L12 8l2 6H2z"/></svg>
    </li>
    <li>martin@plumlinegroup.com
      <svg viewBox="0 0 16 16" aria-hidden="true"><path d="M1 3h14v10H1z M2 4l6 5 6-5v1l-6 5-6-5z" fill-rule="evenodd"/></svg>
    </li>
    <li>www.varkoworks.com
      <svg viewBox="0 0 16 16" aria-hidden="true"><path d="M8 1a7 7 0 1 0 0 14A7 7 0 0 0 8 1zm0 1.3c.9 0 1.8 1.6 2.1 4H5.9C6.2 3.9 7.1 2.3 8 2.3zM2.4 7.3h2.3c0-.4 0-.7.1-1H2.8a5.7 5.7 0 0 0-.4 1zm0 1.4c.1.4.2.7.4 1h2c-.1-.3-.1-.6-.1-1zm3.5 0h4.2c0 .4 0 .7-.1 1H6c0-.3-.1-.6-.1-1zm5.4 0h2.3c-.1.4-.2.7-.4 1h-2c.1-.3.1-.6.1-1zm0-1.4c0-.3 0-.6-.1-1h2c.2.3.3.6.4 1zM8 13.7c-.9 0-1.8-1.6-2.1-3h4.2c-.3 1.4-1.2 3-2.1 3z"/></svg>
    </li>
    <li>18761 52nd Avenue S, Kent, WA 98047
      <svg viewBox="0 0 16 16" aria-hidden="true"><path d="M8 1a5 5 0 0 0-5 5c0 3.5 5 9 5 9s5-5.5 5-9a5 5 0 0 0-5-5zm0 7a2 2 0 1 1 0-4 2 2 0 0 1 0 4z"/></svg>
    </li>
  </ul>
</section>

</body>
</html>
```